I am looking to create a newly designed website for our national leadership conference which is entitled, "The Harbor of Momentum Leadership Summit". The Harbor of Momentum Leadership Summit is a national conference for student leaders that prepares them for career leadership success. The current website can be seen at www.harborofmomentumleadershipsummit.com.

My goal for the new site is to create a more updated, fresh, hip, and exciting look that appeals to the younger generation while also maintaining are professional appeal. The color should be black, white, and gold. We want there to be live videos played and places to insert pictures for the panels as well.

I look forward to seeing you the new creations.

Requirements
Must have
• Ability to play videos on the home page and throughout the website. Also, make sure that the website shows up clearly on an zTablet.
Nice to have
• Nice look

```html
<!DOCTYPE html>
<html lang="en">
<head>
<meta charset="utf-8">
<title>The Harbor of Momentum Leadership Summit</title>
<link href="https://fonts.googleapis.com/css2?family=Raleway:wght@400;500;600;700&family=Open+Sans:ital,wght@0,400;0,600;1,400&display=swap" rel="stylesheet">
<style>
:root{
  --gold:#f0b93a;
  --gold-light:#f7cf5e;
  --gold-deep:#e9a623;
  --gold-text:#e3ac2f;
  --black:#0b0b0b;
  --ink:#222;
  --muted:#555;
  --white:#fff;
  --paper:#f2f2f2;
  --line:#d9d9d9;
}
*{box-sizing:border-box;margin:0;padding:0}
html,body{width:701px;height:1200px;overflow:hidden;background:var(--white)}
body{position:relative;font-family:"Open Sans",Arial,sans-serif;color:var(--ink)}
.abs{position:absolute}

/* header */
.topbar{left:0;top:0;width:701px;height:48px;background:var(--white)}
.btn-register-top{left:547px;top:22px;width:62px;height:18px;background:var(--gold);color:var(--white);font:500 8px "Raleway",sans-serif;display:flex;align-items:center;justify-content:center;gap:3px}
.mainnav{left:0;top:48px;width:701px;height:26px;background:var(--black);z-index:2}
.mainnav a{position:absolute;top:0;height:26px;color:var(--white);font:500 8px "Raleway",sans-serif;line-height:26px;text-decoration:none;letter-spacing:.2px}
.mainnav .sep{position:absolute;top:0;width:1px;height:26px;background:#333}
.brand{left:295px;top:0;width:112px;height:112px;border-radius:50%;background:var(--gold-light);border:4px solid #f6edd4;display:flex;align-items:center;justify-content:center;text-align:center;box-shadow:0 1px 3px rgba(0,0,0,.2);z-index:5}
.brand span{font:700 8.5px "Raleway",sans-serif;line-height:11px;color:#2a2a2a;letter-spacing:.6px;margin-top:30px}

/* hero */
.hero{left:0;top:74px;width:701px;height:258px;background:linear-gradient(90deg,#5e6a4c 0%,#7a6f62 25%,#5a5c6a 55%,#80807a 80%,#5e6650 100%)}
.hero-shade{left:0;top:74px;width:701px;height:258px;background:rgba(20,20,25,.35)}
.hero-title{left:0;top:164px;width:701px;text-align:center;color:var(--white);font:700 30px "Raleway",sans-serif;line-height:36px;letter-spacing:.5px;text-shadow:0 1px 3px rgba(0,0,0,.4)}
.hero-sub{left:0;top:198px;width:701px;text-align:center;color:var(--white);font:700 19px "Raleway",sans-serif;line-height:24px;letter-spacing:.5px}
.dots{left:326px;top:313px;display:flex;gap:3px}
.dots i{width:10px;height:10px;border-radius:50%;background:var(--white);display:block}
.dots i.on{background:var(--gold);border:1.5px solid var(--white)}

/* countdown */
.count{left:0;top:332px;width:701px;height:78px;background:linear-gradient(180deg,var(--gold-light),var(--gold-deep))}
.count svg{position:absolute;left:0;top:0}
.count-label{left:99px;top:354px;color:var(--white);font:500 14px "Raleway",sans-serif;line-height:19px}
.count-label b{font-weight:600;font-size:15.5px}
.unit{top:349px;width:90px;text-align:center;color:var(--white)}
.unit .n{font:400 26px "Raleway",sans-serif;line-height:28px}
.unit .l{font:500 10px "Raleway",sans-serif;line-height:12px;margin-top:3px}
.vline{top:332px;width:1px;height:78px;background:rgba(255,255,255,.35)}

/* intro */
.intro{left:10px;top:410px;width:657px;height:179px;background:linear-gradient(180deg,var(--white) 0%,var(--white) 60%,#ececec 100%)}
.intro-title{left:0;top:440px;width:681px;text-align:center;font:400 17px "Raleway",sans-serif;line-height:20px;color:var(--ink)}
.intro-lead{left:95px;top:465px;width:510px;text-align:center;font-size:7.6px;line-height:12.3px;color:#333}
.intro-body{left:90px;top:498px;width:520px;text-align:center;font-size:6.3px;line-height:12px;color:#555}
.btn-dark{left:318px;top:548px;width:72px;height:21px;background:var(--black);border:2px solid var(--black);outline:1px solid var(--white);outline-offset:-3px;color:var(--white);font:600 8px "Raleway",sans-serif;display:flex;align-items:center;justify-content:center}

/* video */
.video-title{left:95px;top:618px;font:400 16.5px "Raleway",sans-serif;line-height:20px;color:var(--gold-text)}
.video-lead{left:95px;top:645px;width:260px;font-size:7.8px;line-height:12.5px;color:#555}
.video-body{left:95px;top:677px;width:260px;font-size:6.5px;line-height:12px;color:#666}
.btn-outline{left:96px;top:719px;width:66px;height:20px;border:1.5px solid var(--gold);color:var(--gold-text);font:600 7px "Raleway",sans-serif;display:flex;align-items:center;justify-content:center}
.player{left:380px;top:614px;width:227px;height:130px;background:#2b2b2b;box-shadow:0 1px 2px rgba(0,0,0,.3)}
.player .frame{position:absolute;left:2px;top:2px;width:223px;height:111px;background:linear-gradient(180deg,#d8d8d8,#a9a9a9)}
.player svg{position:absolute;left:0;top:0}

/* features */
.features{left:95px;top:797px;width:512px;height:107px;border:1px solid var(--line);display:flex}
.feature{width:170.6px;height:105px;text-align:center;padding-top:22px;position:relative}
.feature.gold{background:linear-gradient(180deg,var(--gold-light),var(--gold-deep))}
.feature h3{font:500 10px "Raleway",sans-serif;line-height:13px;color:var(--gold-text);letter-spacing:.2px}
.feature p{font:500 7.5px "Raleway",sans-serif;line-height:13px;color:var(--gold-text);margin-top:2px}
.feature.gold h3,.feature.gold p{color:var(--white)}
.badge{position:absolute;left:50%;transform:translateX(-50%)}

/* testimonials */
.testi{left:0;top:941px;width:701px;height:180px;background:linear-gradient(90deg,#3a3a3a,#4b4b4b 40%,#2e2e2e 70%,#3d3d3d)}
.testi-title{left:0;top:965px;width:701px;text-align:center;color:var(--white);font:400 15px "Raleway",sans-serif;line-height:18px;letter-spacing:.4px}
.avatar{width:48px;height:48px;border-radius:50%;background:linear-gradient(160deg,#c9a98a,#8c7765);border:2.5px solid var(--white)}
.quote{width:118px;color:var(--white);font-style:italic;font-size:6.5px;line-height:11.5px}
.quote::before{content:"\201C";position:absolute;left:-10px;top:-4px;font:400 17px Georgia,serif;font-style:normal}
.who{color:var(--white);font-size:7.5px;line-height:13px}
.who small{display:block;font-size:6.6px;color:#ddd}

/* footer */
.footer{left:0;top:1121px;width:701px;height:79px;background:var(--paper)}
.footnav{left:0;top:1142px;width:701px;display:flex;justify-content:center;gap:12px;font:500 8px "Raleway",sans-serif;line-height:10px;color:#222}
.copy{left:0;top:1160px;width:701px;text-align:center;font-size:6.7px;color:#666}
.social{left:307px;top:1176px;display:flex;gap:2px}
.social i{display:block;width:15px;height:15px;border-radius:50%;border:1.2px solid #222}
</style>
</head>
<body>

<header>
  <div class="abs topbar"></div>
  <div class="abs btn-register-top">
    <svg width="7" height="8" viewBox="0 0 7 8"><circle cx="3.5" cy="2" r="2" fill="#fff"/><path d="M0 8c0-3 1.5-4 3.5-4S7 5 7 8z" fill="#fff"/></svg>
    REGISTER
  </div>
  <nav class="abs mainnav">
    <a style="left:106px">HOME</a><span class="sep" style="left:139px"></span>
    <a style="left:152px">ABOUT US</a><span class="sep" style="left:203px"></span>
    <a style="left:215px">CONFRENCE</a>
    <a style="left:425px">TETSTIMONIAL</a><span class="sep" style="left:487px"></span>
    <a style="left:501px">VIDEO</a><span class="sep" style="left:535px"></span>
    <a style="left:547px">CONTACT</a>
  </nav>
  <div class="abs brand"><span>HARBOR OF<br>MOMENTUM</span></div>
</header>

<section>
  <div class="abs hero" role="img" aria-label="Photo of four students gathered around a laptop at a café table"></div>
  <div class="abs hero-shade"></div>
  <h1 class="abs hero-title">NATIONAL CONFERENCE</h1>
  <h2 class="abs hero-sub">FOR STUDENT LEADERS</h2>
  <div class="abs dots"><i class="on"></i><i></i><i></i><i></i></div>
</section>

<section>
  <div class="abs count">
    <svg width="320" height="78" viewBox="0 0 320 78"><defs><linearGradient id="blk" x1="0" y1="0" x2="0" y2="1"><stop offset="0" stop-color="#222"/><stop offset="1" stop-color="#050505"/></linearGradient></defs><polygon points="0,0 290,0 314,39 290,78 0,78" fill="url(#blk)"/></svg>
  </div>
  <div class="abs count-label">6TH ANNUAL CONFERENCE<br><b>COUNTDOWN</b></div>
  <div class="abs vline" style="left:405px"></div>
  <div class="abs vline" style="left:496px"></div>
  <div class="abs unit" style="left:316px"><div class="n">00</div><div class="l">HOURS</div></div>
  <div class="abs unit" style="left:406px"><div class="n">00</div><div class="l">MINUTES</div></div>
  <div class="abs unit" style="left:500px"><div class="n">00</div><div class="l">SECONDS</div></div>
</section>

<section>
  <div class="abs intro"></div>
  <h2 class="abs intro-title">The Harbor of Momentum Leadership Summit</h2>
  <p class="abs intro-lead">for a transformational leadership experience that will connect you with an incredible diverse leadership network of students and professionals that provide you with the inspiration and leadership/professional skills needed to take your life to the next level!</p>
  <p class="abs intro-body">Mauris vel lacus vitae felis vestibulum volutpat E eu imperdiet ac nisl Cum sociis natoque penatibus et magnis dis parturient montes nascetur ridiculus mus In iaculis facilisis massa Etiam eu urna Sed porta Suspendisse quam leo molestie sed luctus quis feugiat in pede Fusce tellus Sed metus augue convallis et vehicula ut pulvinar eu ante Integer orci tellus tristique vitae consequat neceger quis urna Ut ante enim dapibus malesuada fri</p>
  <div class="abs btn-dark">REGISTER</div>
</section>

<section>
  <h2 class="abs video-title">Watch Our Latest Video</h2>
  <p class="abs video-lead">Ut nisi erat fermentum vel congue id euismod in elit Fusce ultricies orci ac feugiat suscipit leo massa sodales</p>
  <p class="abs video-body">Aelit et scelerisque mi tortor at ipsum cligula augue bibendum accumsan vestibulum ut commodo a mi Morbi ornare gravida elit Integer congue augue et malesuada odales velit et scelerisque mi tortor</p>
  <div class="abs btn-outline">LEARN MORE</div>
  <div class="abs player">
    <div class="frame" role="img" aria-label="Video still of three women seated in a panel discussion"></div>
    <svg width="227" height="130" viewBox="0 0 227 130">
      <circle cx="113" cy="60" r="13" fill="#fff"/>
      <polygon points="109,53 109,67 120,60" fill="#111"/>
      <polygon points="6,119 6,126 12,122.5" fill="#fff"/>
      <rect x="17" y="120.5" width="172" height="3" rx="1.5" fill="#ddd"/>
      <rect x="17" y="120.5" width="69" height="3" rx="1.5" fill="#3d7fd3"/>
      <polygon points="206,120 209,120 212,117.5 212,127.5 209,125 206,125" fill="#fff"/>
      <path d="M214 120 q2 2.5 0 5" stroke="#fff" stroke-width="1" fill="none"/>
    </svg>
  </div>
</section>

<section class="abs features">
  <div class="feature">
    <h3>VOTED AS TOP STUDENT</h3>
    <p>LEADERSHIP PROGRAM OF THE<br>YEAR IN 2014</p>
    <svg class="badge" style="top:82px" width="86" height="14"><rect width="86" height="14" fill="#d6d6d6"/></svg>
  </div>
  <div class="feature gold">
    <h3>NETWORK WITH</h3>
    <p>EXECUTIVES</p>
    <svg class="badge" style="top:64px" width="74" height="22"><rect width="74" height="22" fill="rgba(255,255,255,.55)"/></svg>
  </div>
  <div class="feature">
    <h3>CONNECT WITH OTHER</h3>
    <p>STUDENT LEADERS FROM</p>
    <svg class="badge" style="top:62px" width="30" height="30"><rect width="30" height="30" fill="#c8d3e6"/></svg>
  </div>
</section>

<section>
  <div class="abs testi" role="img" aria-label="Dimmed black and white photo of students in a classroom"></div>
  <h2 class="abs testi-title">TESTIMONIALS</h2>

  <div class="abs avatar" style="left:90px;top:998px" role="img" aria-label="Student portrait"></div>
  <p class="abs quote" style="left:145px;top:1003px">Mauris vel lacus vitae felis vestibulum volutpat E eu imperdiet ac nisl Cum sociis natoque penat ibus et magnis dis parturient montes nascetur ridi</p>
  <p class="abs who" style="left:144px;top:1068px">By Student Name<small>Location</small></p>

  <div class="abs avatar" style="left:267px;top:997px" role="img" aria-label="Student portrait"></div>
  <p class="abs quote" style="left:322px;top:1001px">Pellentesque faucibus Ut accumsan ultricies elit Maecenas at justo id velit placerat molestie Donec dictum lectus non odio Cras a ante vitae enim iaculis aliquam</p>
  <p class="abs who" style="left:322px;top:1068px">By Student Name<small>Location</small></p>

  <div class="abs avatar" style="left:444px;top:999px" role="img" aria-label="Student portrait"></div>
  <p class="abs quote" style="left:499px;top:997px">Mauris vel lacus vitae felis vestibulum volutpat E eu imperdiet ac nisl Cum sociis natoque penat ibus et magnis dis parturient montes nascetur ridi</p>
  <p class="abs who" style="left:497px;top:1068px">By Student Name<small>Location</small></p>
</section>

<footer>
  <div class="abs footer"></div>
  <nav class="abs footnav"><span>HOME</span><span>ABOUT US</span><span>CONFRENCE</span><span>TETSTIMONIAL</span><span>VIDEO</span><span>CONTACT</span></nav>
  <p class="abs copy">© 2015 Company Name &nbsp;All right reserved</p>
  <div class="abs social"><i></i><i></i><i></i><i></i></div>
</footer>

</body>
</html>
```